UK Online Escort Directory Requires a Redesigned Email Marketing Campaign (4 emails total)

These emails should be designed as marketing emails that will be sent out to approx 10,000 potential customers on a by monthly basis. The designs should be innovative, professional designs that are capable of capturing a readers attention in the blink of an eye.

We have posted this job as our in-house design capabilities are not able to create professional email designs, we therefore require a designer to redesign our email marketing campaign (4 emails total) to a professional level.

The content of the emails will be provided, along with the 5 emails that we are currently sending and the company logo. This should give the potential designer all that they need to redesign the campaign to a professional level.

Please see attached brief for more information on what is required from each individual email.

Target Market(s)

Escorts throughout the UK

Industry/Entity Type

Escort

Font styles to use
Serif
Sans Serif

Requirements
Must have
• Instant recognition of what's being offered.
Nice to have
• Imaginative / inspirational designs.
Should not have
• Any unnecessary wording or text.

```html
<!DOCTYPE html>
<html lang="en">
<head>
<meta charset="utf-8">
<title>Velvetlist-uk.com – Weekly Ad Report</title>
<link rel="stylesheet" href="https://fonts.googleapis.com/css2?family=Open+Sans:wght@400;600;700&family=Oswald:wght@400;500&display=swap">
<style>
  :root {
    --white: #ffffff;
    --brand: #9fb6d8;
    --tagline: #5a7dc0;
    --ribbon: #a6e1e3;
    --ribbon-dark: #7ccbd0;
    --rule: #a6e1e3;
    --stats-band: #d9eda3;
    --ink: #1a1a1a;
    --cream: #fdf8cc;
    --card: #c5606e;
    --photo: #d8b79a;
    --star: #f3b51c;
    --button: #000000;
    --muted: #8a8a8a;
  }
  * { margin: 0; padding: 0; box-sizing: border-box; }
  html, body { width: 1200px; height: 1198px; overflow: hidden; background: var(--white); }
  body { font-family: "Open Sans", Arial, sans-serif; color: var(--ink); }
  .email { position: relative; width: 1200px; height: 1198px; background: var(--white); }

  .masthead { position: absolute; left: 0; top: 0; width: 1200px; height: 296px; background: var(--white); }
  .brand-name {
    position: absolute; left: 0; top: 42px; width: 1200px; text-align: center;
    font-family: "Open Sans", Arial, sans-serif; font-weight: 400;
    font-size: 104px; letter-spacing: -1px; color: var(--brand); line-height: 1;
  }
  .tagline {
    position: absolute; left: 52px; top: 158px;
    font-weight: 700; font-size: 26px; color: var(--tagline);
  }

  .stats-band { position: absolute; left: 0; top: 296px; width: 1200px; height: 174px; background: var(--stats-band); }
  .rule { position: absolute; left: 0; top: 288px; width: 1200px; height: 8px; background: var(--rule); }
  .ribbon { position: absolute; left: 240px; top: 254px; width: 720px; height: 78px; }
  .ribbon-text {
    position: absolute; left: 240px; top: 254px; width: 720px; height: 70px;
    display: flex; align-items: center; justify-content: center;
    color: var(--white); font-weight: 700; font-size: 32px; letter-spacing: 0.5px;
  }
  .stats {
    position: absolute; left: 0; top: 62px; width: 1200px; height: 92px; line-height: 92px;
    text-align: center; font-size: 34px; color: var(--ink); white-space: nowrap;
  }
  .stats .figure { font-family: "Oswald", Arial, sans-serif; font-weight: 500; font-size: 76px; vertical-align: -4px; }

  .listing { position: absolute; left: 0; top: 470px; width: 1200px; height: 660px; background: var(--cream); }
  .card { position: absolute; left: 46px; top: 140px; width: 1110px; height: 320px; background: var(--card); }
  .photo-frame { position: absolute; left: 76px; top: 70px; width: 244px; height: 360px; background: var(--white); }
  .photo { position: absolute; left: 10px; top: 10px; width: 224px; height: 340px;
    background: linear-gradient(160deg, #e6c7a0 0%, var(--photo) 55%, #b98f73 100%); }
  .rating { position: absolute; left: 768px; top: 88px; display: flex; align-items: center; gap: 14px; font-size: 28px; }
  .stars { display: flex; gap: 4px; }
  .name { position: absolute; left: 346px; top: 172px; color: var(--white); white-space: nowrap; }
  .name strong { font-size: 32px; font-weight: 700; }
  .name span { font-size: 28px; margin-left: 10px; }
  .blurb { position: absolute; left: 346px; top: 240px; width: 760px; color: var(--white); font-size: 28px; line-height: 48px; }

  .button {
    position: absolute; top: 504px; width: 254px; height: 66px; background: var(--button);
    color: var(--white); font-size: 28px; font-weight: 600;
    display: flex; align-items: center; justify-content: center;
  }
  .button.view { left: 180px; }
  .button.post { left: 768px; }
  .link { position: absolute; top: 586px; font-size: 28px; color: var(--ink); text-align: center; }
  .link.view { left: 40px; width: 560px; }
  .link.post { left: 600px; width: 580px; }

  .footer { position: absolute; left: 0; top: 1130px; width: 1200px; height: 68px;
    display: flex; align-items: center; justify-content: center; font-size: 24px; color: var(--muted); }
</style>
</head>
<body>
<main class="email">
  <header class="masthead">
    <div class="brand-name">velvetlist-uk.com</div>
    <div class="tagline">The Escort Directory</div>
  </header>

  <section class="stats-band">
    <p class="stats"><span class="figure">963</span> times&nbsp; and produced <span class="figure">150</span> phone calls for just £<span class="figure">40.49</span>pm</p>
  </section>
  <div class="rule"></div>
  <svg class="ribbon" viewBox="0 0 720 78" aria-hidden="true">
    <polygon points="0,8 40,8 40,78 0,78 18,43" fill="var(--ribbon-dark)"/>
    <polygon points="720,8 680,8 680,78 720,78 702,43" fill="var(--ribbon-dark)"/>
    <rect x="24" y="0" width="672" height="70" fill="var(--ribbon)"/>
  </svg>
  <div class="ribbon-text">LAST WEEK THIS AD WAS VIEWED</div>

  <section class="listing">
    <div class="card"></div>
    <div class="photo-frame">
      <div class="photo" role="img" aria-label="Profile photo of the advertised companion"></div>
    </div>
    <div class="rating">
      <span>Recommended</span>
      <span class="stars">
        <svg width="30" height="30" viewBox="0 0 24 24"><polygon points="12,1 15,9 23,9 17,14 19,22 12,17 5,22 7,14 1,9 9,9" fill="var(--star)"/></svg>
        <svg width="30" height="30" viewBox="0 0 24 24"><polygon points="12,1 15,9 23,9 17,14 19,22 12,17 5,22 7,14 1,9 9,9" fill="var(--star)"/></svg>
        <svg width="30" height="30" viewBox="0 0 24 24"><polygon points="12,1 15,9 23,9 17,14 19,22 12,17 5,22 7,14 1,9 9,9" fill="var(--star)"/></svg>
        <svg width="30" height="30" viewBox="0 0 24 24"><polygon points="12,1 15,9 23,9 17,14 19,22 12,17 5,22 7,14 1,9 9,9" fill="var(--star)"/></svg>
        <svg width="30" height="30" viewBox="0 0 24 24"><polygon points="12,1 15,9 23,9 17,14 19,22 12,17 5,22 7,14 1,9 9,9" fill="var(--star)"/></svg>
      </span>
    </div>
    <p class="name"><strong>Marisol,24</strong><span>Pimlico, Westminster, Chelsa Escort</span></p>
    <p class="blurb">One of our Top 20 London escorts, this very attractive, well proportioned blonde busty escort always has a smile on her face.</p>

    <div class="button view">Take a look@</div>
    <div class="button post">Post an add@</div>
    <p class="link view">www.velvetlist-uk.com/</p>
    <p class="link post">www.velvetlist-uk.com/post/add/</p>
  </section>

  <footer class="footer">Copyright 2016 Velvetlist-uk.com All Rights Reserved</footer>
</main>
</body>
</html>
```